GJ & DW Fencing Pty Ltd

We already have an existing logo created by Pixel Harbour however we have restructured to a company. We would like someone to add Pty Ltd to our business name please.

Colors

Designer to choose only greyscale colors for use in the design.

```html
<!DOCTYPE html>
<html lang="en">
<head>
<meta charset="utf-8">
<title>GJ &amp; DW Fencing Pty Ltd — Business Card</title>
<link rel="stylesheet" href="https://fonts.googleapis.com/css2?family=Cinzel:wght@400;600&family=Josefin+Sans:wght@300;400&display=swap">
<style>
  :root {
    --page-bg: #e6e6e6;
    --card-black: #161616;
    --card-charcoal: #3a3a3a;
    --card-white: #f4f4f4;
    --stripe: #2a2a2a;
    --ink: #222222;
    --ink-soft: #3c3c3c;
    --logo-white: #f7f7f7;
  }
  * { margin: 0; padding: 0; box-sizing: border-box; }
  html, body {
    width: 1200px; height: 1022px; overflow: hidden;
    background: var(--page-bg);
  }
  .business-card {
    position: absolute;
    left: 100px; top: 225px;
    width: 1000px; height: 572px;
    border-radius: 18px;
    overflow: hidden;
    background: radial-gradient(ellipse at 40% 45%, var(--card-charcoal) 0%, var(--card-black) 65%);
    box-shadow: 0 18px 40px rgba(0,0,0,0.25);
  }
  .card-waves { position: absolute; inset: 0; width: 100%; height: 100%; }
  .company-logo {
    position: absolute;
    left: 60px; top: 250px;
    display: flex; align-items: center; gap: 16px;
    color: var(--logo-white);
    font-family: "Cinzel", serif;
    font-weight: 600;
  }
  .logo-dot {
    width: 60px; height: 60px; border-radius: 50%;
    background: var(--logo-white);
    flex: none;
  }
  .logo-name { line-height: 1; white-space: nowrap; }
  .logo-initials { display: block; font-size: 60px; letter-spacing: 1px; }
  .logo-suffix { display: block; font-size: 24px; letter-spacing: 2px; margin-top: 6px; }
  .contact-block {
    position: absolute;
    right: 50px; top: 50px;
    text-align: right;
    color: var(--ink);
  }
  .person-name {
    font-family: "Cinzel", serif;
    font-weight: 400;
    font-size: 28px;
    letter-spacing: 4px;
    margin-bottom: 20px;
    white-space: nowrap;
  }
  .contact-list { list-style: none; }
  .contact-item {
    display: flex; justify-content: flex-end; align-items: center; gap: 16px;
    font-family: "Josefin Sans", sans-serif;
    font-weight: 300;
    font-size: 20px;
    color: var(--ink-soft);
    height: 40px;
    white-space: nowrap;
  }
  .contact-icon { width: 24px; height: 24px; flex: none; }
</style>
</head>
<body>
  <main class="business-card">
    <svg class="card-waves" viewBox="0 0 1000 572" preserveAspectRatio="none" aria-hidden="true">
      <path d="M600 0 C 590 150, 560 270, 470 380 C 390 470, 250 540, 120 572 L1000 572 L1000 0 Z" fill="var(--card-white)"/>
      <path d="M590 120 C 575 250, 520 350, 430 420 C 340 490, 220 545, 120 572 L 170 572 C 280 545, 390 495, 470 425 C 545 355, 580 250, 590 120 Z" fill="var(--stripe)"/>
    </svg>

    <div class="company-logo">
      <span class="logo-dot"></span>
      <span class="logo-name">
        <span class="logo-initials">GJ &amp; DW</span>
        <span class="logo-suffix">FENCING PTY LTD</span>
      </span>
    </div>

    <section class="contact-block">
      <h1 class="person-name">TOM HALLBROOK</h1>
      <ul class="contact-list">
        <li class="contact-item">PO Box 415 CALDER WA 6409
          <svg class="contact-icon" viewBox="0 0 26 26"><circle cx="13" cy="13" r="13" fill="var(--ink)"/><path d="M7 13 L13 7.5 L19 13 M9 12 V18 H17 V12" fill="none" stroke="#fff" stroke-width="1.8"/></svg>
        </li>
        <li class="contact-item">0400 555 219
          <svg class="contact-icon" viewBox="0 0 26 26"><circle cx="13" cy="13" r="13" fill="var(--ink)"/><path d="M9 7.5 L11.5 10.5 L10 12 C11 14.5 12 15.5 14 16.5 L15.5 15 L18.5 17.5 L16.5 19 C12 18.5 7.5 14 7 9.5 Z" fill="#fff"/></svg>
        </li>
        <li class="contact-item">gjdwfencing@mailbox.com
          <svg class="contact-icon" viewBox="0 0 26 26"><circle cx="13" cy="13" r="13" fill="var(--ink)"/><rect x="7" y="8.5" width="12" height="9" fill="none" stroke="#fff" stroke-width="1.6"/><path d="M7 8.5 L13 13.5 L19 8.5" fill="none" stroke="#fff" stroke-width="1.6"/></svg>
        </li>
      </ul>
    </section>
  </main>
</body>
</html>
```